High-end construction company needs a business card design

We need a modern looking business card that draws people in, is memorable and looks so good people will want to sick it on their fridges.
On the first side what is needed are:
Logo
My name - Tomasz Brelwik
Title - Managing Director
Website - www.varkelt.co.uk
Email - tomasz@varkelt.co.uk
Telephone - 020 5194 6281
Mobile - 07845139072
On the back side was is needed is a list of all the services we provide:
-Kitchen Renovations
-Bathroom Renovations
-House Renovations
-Garage Conversions
-Extensions
-Loft Conversions
-Conservatories
-Carpentry
-Tiling
-Electrical
-Plumbing & Heating
-Bricklaying
-Landscaping
-Decorating
-Plastering
We would like the colours to be the same shades as on the logo with grey or black for the words.
Target Market(s)
Anyone who needs building work done
Contact Information for Business Card
This business card is for a construction company which strives to deliver excellent service and quality.
The look and feel of the card should represent this.
Requirements
Must have
- On the first side what is needed are:
Logo
My name - Tomasz Brelwik
Title - Managing Director
Website - www.varkelt.co.uk
Email - tomasz@varkelt.co.uk
Telephone - 020 5194 6281
Mobile - 07845139072
Nice to have
- Cool looking features

```html
<!DOCTYPE html>
<html lang="en">
<head>
<meta charset="utf-8">
<title>Varkelt Construction Ltd – Business Card</title>
<link href="https://fonts.googleapis.com/css2?family=Lato:wght@400;700;900&display=swap" rel="stylesheet">
<style>
  :root {
    --bg: #d3d4cf;
    --card: #ffffff;
    --green: #5bb33a;
    --green-dark: #3f8f2a;
    --ink: #3d3d3d;
    --ink-soft: #555555;
  }
  * { box-sizing: border-box; margin: 0; padding: 0; }
  html, body {
    width: 1200px; height: 801px; overflow: hidden;
    background: var(--bg);
    font-family: "Lato", sans-serif;
    color: var(--ink);
  }
  .stage {
    position: relative; width: 1200px; height: 801px;
    display: flex; align-items: center; justify-content: center; gap: 50px;
  }
  .card {
    position: relative;
    width: 530px; height: 304px;
    background: var(--card);
    border-bottom: 5px solid var(--green);
    box-shadow: 0 10px 24px rgba(0,0,0,0.18);
  }

  /* Front */
  .front { display: flex; align-items: center; }
  .brand {
    width: 250px; height: 100%;
    display: flex; align-items: center; justify-content: center; gap: 10px;
  }
  .brand-mark { width: 18px; height: 18px; background: var(--green); flex: none; }
  .brand-name {
    font-weight: 900; color: var(--green); font-size: 22px; line-height: 1.15;
    letter-spacing: 0.5px; text-transform: uppercase;
  }
  .front .divider {
    width: 1px; height: 110px; background: var(--green); opacity: 0.8;
  }
  .details { padding-left: 28px; }
  .person-name { font-size: 27px; font-weight: 700; color: var(--green-dark); line-height: 1.1; }
  .person-title { font-size: 14px; color: var(--ink-soft); margin-top: 4px; margin-bottom: 16px; }
  .contact-list { list-style: none; }
  .contact-list li {
    display: flex; align-items: center; gap: 10px;
    font-size: 14px; color: var(--ink); line-height: 1; margin-bottom: 9px;
  }
  .contact-list svg { width: 15px; height: 15px; flex: none; }
  .accent { color: var(--green); }

  /* Back */
  .back { display: flex; align-items: center; justify-content: center; }
  .services {
    list-style: none; font-size: 15.5px; color: var(--ink); line-height: 1.55;
  }
  .services li { display: flex; align-items: center; gap: 12px; }
  .services li::after, .services.right li::before {
    content: ""; width: 5px; height: 5px; border-radius: 50%; background: var(--green-dark); flex: none;
  }
  .services.left { text-align: right; }
  .services.left li { justify-content: flex-end; }
  .services.right li::after { display: none; }
  .back .divider {
    width: 1px; height: 180px; background: var(--green); margin: 0 26px;
  }
</style>
</head>
<body>
<main class="stage">
  <section class="card front" aria-label="Business card front">
    <div class="brand">
      <span class="brand-mark"></span>
      <span class="brand-name">Varkelt<br>Construction Ltd</span>
    </div>
    <div class="divider"></div>
    <div class="details">
      <h1 class="person-name">Tomasz Brelwik</h1>
      <p class="person-title">Managing Director</p>
      <ul class="contact-list">
        <li>
          <svg viewBox="0 0 16 16" aria-hidden="true"><path fill="#5bb33a" d="M3 1.5l2.5-.5 1.5 3.5-1.8 1.2a9 9 0 0 0 5 5l1.2-1.8 3.5 1.5-.5 2.5c-.3 1-1.3 1.6-2.3 1.4C7 13.5 2.5 9 1.6 3.8 1.4 2.8 2 1.8 3 1.5z"/></svg>
          020 5194 6281
        </li>
        <li>
          <svg viewBox="0 0 16 16" aria-hidden="true"><rect x="4" y="1" width="8" height="14" rx="1.5" fill="none" stroke="#5bb33a" stroke-width="1.6"/><circle cx="8" cy="12.5" r="0.9" fill="#5bb33a"/></svg>
          07845139072
        </li>
        <li>
          <svg viewBox="0 0 16 16" aria-hidden="true"><rect x="1" y="3" width="14" height="10" rx="1" fill="#5bb33a"/><path d="M1.5 3.5L8 9l6.5-5.5" fill="none" stroke="#fff" stroke-width="1.3"/></svg>
          tomasz@varkelt.co.uk
        </li>
        <li>
          <svg viewBox="0 0 16 16" aria-hidden="true"><g fill="none" stroke="#5bb33a" stroke-width="1.3"><circle cx="8" cy="8" r="6.5"/><ellipse cx="8" cy="8" rx="3" ry="6.5"/><path d="M1.5 8h13M2.5 4.8h11M2.5 11.2h11"/></g></svg>
          <span>www.<span class="accent">varkelt</span>.co.uk</span>
        </li>
      </ul>
    </div>
  </section>

  <section class="card back" aria-label="Business card back – services">
    <ul class="services left">
      <li>Kitchen Renovations</li>
      <li>Bathroom Renovations</li>
      <li>House Renovations</li>
      <li>Garage Conversions</li>
      <li>Extensions</li>
      <li>Loft Conversions</li>
      <li>Conservatories</li>
      <li>Carpentry</li>
    </ul>
    <div class="divider"></div>
    <ul class="services right">
      <li>Tiling</li>
      <li>Electrical</li>
      <li>Plumbing &amp; Heating</li>
      <li>Bricklaying</li>
      <li>Landscaping</li>
      <li>Decorating</li>
      <li>Plastering</li>
    </ul>
  </section>
</main>
</body>
</html>
```